Freelance business trainer needs a new business card

My business is called Brontlearn. I provide training in the workplace on management, coaching and mentoring, and customer service topics for a variety of businesses, colleges and private training providers, and teach on management programs. I need a professional but eye catching business card. Business colours grey and orange. My name Marion Tadwick; Tel 07382 415067; email mtadwick@brontlearn.co.uk; website www.brontlearn.co.uk.
Happy to have some sort of logo on front and details on back or all on one side
Target Market(s)
SME businesses and colleges - workshops i run are for adults in the workplace
Industry/Entity Type
Training
Look and feel

```html
<!DOCTYPE html>
<html lang="en">
<head>
<meta charset="utf-8">
<title>Brontlearn – Business Card</title>
<link rel="stylesheet" href="https://fonts.googleapis.com/css2?family=Ubuntu:wght@400&display=swap">
<style>
  :root {
    --orange: #e07418;
    --stripe-grey: #d7d7d5;
    --stripe-white: #fafaf8;
    --logo-grey: #5e6a72;
    --ink: #1c1c1c;
    --backdrop: #ececec;
    --white: #ffffff;
  }
  * { box-sizing: border-box; margin: 0; padding: 0; }
  html, body {
    width: 1200px;
    height: 800px;
    overflow: hidden;
    background: var(--backdrop);
    font-family: "Ubuntu", sans-serif;
  }
  .card {
    position: absolute;
    left: 180px;
    top: 128px;
    width: 840px;
    height: 544px;
    background: var(--orange);
    overflow: hidden;
    box-shadow: 0 6px 22px rgba(0,0,0,0.12);
  }
  .brand {
    position: absolute;
    left: 72px;
    top: 58px;
    display: flex;
    align-items: center;
    gap: 22px;
  }
  .brand-disc {
    width: 104px;
    height: 104px;
    border-radius: 50%;
    background: var(--white);
  }
  .brand-name {
    font-size: 58px;
    font-weight: 400;
    color: var(--logo-grey);
    letter-spacing: 0.5px;
  }
  .holder-name {
    position: absolute;
    right: 28px;
    top: 170px;
    font-size: 34px;
    color: var(--white);
    letter-spacing: 0.3px;
  }
  .contact-list {
    position: absolute;
    left: 0;
    top: 290px;
    width: 590px;
    list-style: none;
  }
  .contact-row {
    display: flex;
    align-items: center;
    height: 70px;
    padding-left: 42px;
    gap: 26px;
    font-size: 27px;
    color: var(--ink);
  }
  .contact-row:nth-child(odd) { background: var(--stripe-white); }
  .contact-row:nth-child(even) { background: var(--stripe-grey); }
  .contact-row:last-child { height: 78px; }
  .contact-icon { width: 28px; height: 28px; flex: none; }
  .divider {
    position: absolute;
    left: 590px;
    top: 228px;
    width: 8px;
    height: 245px;
    background: var(--orange);
  }
  .side-stripes {
    position: absolute;
    left: 598px;
    top: 228px;
    width: 242px;
  }
  .side-stripe { height: 72px; background: var(--stripe-grey); }
  .side-stripe.is-light { height: 62px; background: var(--stripe-white); }
  .side-stripe.is-tall { height: 111px; }
</style>
</head>
<body>
  <article class="card">
    <div class="brand">
      <div class="brand-disc"></div>
      <span class="brand-name">Brontlearn</span>
    </div>

    <p class="holder-name">Marion Tadwick</p>

    <ul class="contact-list">
      <li class="contact-row">
        <svg class="contact-icon" viewBox="0 0 28 28" aria-hidden="true">
          <rect x="3" y="5" width="22" height="6" rx="3" fill="#e07418"/>
          <rect x="6" y="11" width="16" height="13" rx="2" fill="#e07418"/>
          <circle cx="14" cy="17.5" r="3.6" fill="#fafaf8"/>
        </svg>
        <span>07382 415067</span>
      </li>
      <li class="contact-row">
        <svg class="contact-icon" viewBox="0 0 28 28" aria-hidden="true">
          <rect x="2" y="6" width="24" height="17" fill="#e07418"/>
          <path d="M2 6 L14 16 L26 6" fill="none" stroke="#d7d7d5" stroke-width="2"/>
        </svg>
        <span>mtadwick@brontlearn.co.uk</span>
      </li>
      <li class="contact-row">
        <svg class="contact-icon" viewBox="0 0 28 28" aria-hidden="true">
          <circle cx="14" cy="14" r="11" fill="#e07418"/>
          <g fill="none" stroke="#fafaf8" stroke-width="1.4">
            <ellipse cx="14" cy="14" rx="4.5" ry="11"/>
            <line x1="3" y1="14" x2="25" y2="14"/>
            <line x1="14" y1="3" x2="14" y2="25"/>
            <line x1="5" y1="8.5" x2="23" y2="8.5"/>
            <line x1="5" y1="19.5" x2="23" y2="19.5"/>
          </g>
        </svg>
        <span>www.brontlearn.co.uk</span>
      </li>
    </ul>

    <div class="divider"></div>

    <div class="side-stripes">
      <div class="side-stripe"></div>
      <div class="side-stripe is-light"></div>
      <div class="side-stripe is-tall"></div>
    </div>
  </article>
</body>
</html>
```